The Linen Loft Co

We need a business card design for our wardrobe company.
Please visit our website www.gentlelinenlofts.com to get an idea of who we are.

```html
<!DOCTYPE html>
<html lang="en">
<head>
<meta charset="utf-8">
<title>The Linen Loft Co – Business Card</title>
<link rel="stylesheet" href="https://fonts.googleapis.com/css2?family=Roboto:wght@400;500;700&display=swap">
<style>
  :root {
    --page-bg: #e9e9e9;
    --card-bg: #ffffff;
    --ink: #111111;
    --ink-soft: #4a4a4a;
    --ink-muted: #a8a8a8;
    --rule: #cfcfcf;
    --band: #000000;
    --band-line: #9a9a9a;
  }
  * { box-sizing: border-box; margin: 0; padding: 0; }
  html, body {
    width: 1200px;
    height: 989px;
    overflow: hidden;
    background: var(--page-bg);
    font-family: "Roboto", Arial, sans-serif;
  }
  .card {
    position: absolute;
    left: 50px;
    top: 175px;
    width: 1100px;
    height: 640px;
    background: var(--card-bg);
    box-shadow: 0 2px 8px rgba(0,0,0,0.12);
  }
  .brand-mark {
    position: absolute;
    left: 92px;
    top: 292px;
    width: 78px;
    height: 78px;
    background: var(--ink);
  }
  .brand-text {
    position: absolute;
    left: 253px;
    top: 300px;
    width: 272px;
    display: flex;
    flex-direction: column;
    align-items: center;
    gap: 12px;
  }
  .brand-name {
    font-weight: 500;
    font-size: 22px;
    line-height: 1;
    color: var(--ink);
    text-transform: uppercase;
    white-space: nowrap;
  }
  .brand-tagline {
    font-weight: 500;
    font-size: 19px;
    line-height: 1;
    color: var(--ink);
    white-space: nowrap;
  }
  .divider {
    position: absolute;
    left: 557px;
    top: 172px;
    width: 2px;
    height: 296px;
    background: linear-gradient(to bottom, rgba(207,207,207,0), var(--rule) 15%, var(--rule) 85%, rgba(207,207,207,0));
  }
  .details {
    position: absolute;
    left: 587px;
    top: 178px;
  }
  .person-name {
    font-weight: 700;
    font-size: 42px;
    line-height: 1.1;
    color: var(--ink);
  }
  .person-title {
    font-weight: 500;
    font-size: 28px;
    line-height: 1.1;
    color: var(--ink-muted);
  }
  .address {
    margin-top: 20px;
    font-size: 27px;
    line-height: 34px;
    color: var(--ink-soft);
  }
  .contacts { margin-top: 14px; list-style: none; }
  .contacts li {
    display: flex;
    align-items: center;
    gap: 12px;
    font-size: 27px;
    line-height: 34px;
    color: var(--ink-soft);
  }
  .contacts svg { width: 25px; height: 25px; flex: none; fill: var(--ink); }
  .footer-line {
    position: absolute;
    left: 0; right: 0;
    top: 600px;
    height: 4px;
    background: var(--band-line);
  }
  .footer-band {
    position: absolute;
    left: 0; right: 0;
    top: 608px;
    height: 32px;
    background: var(--band);
  }
</style>
</head>
<body>
  <section class="card">
    <div class="brand-mark"></div>
    <div class="brand-text">
      <span class="brand-name">The Linen Loft Co</span>
      <span class="brand-tagline">Made to Measure, Always</span>
    </div>

    <div class="divider"></div>

    <div class="details">
      <h1 class="person-name">Daniel Hartley</h1>
      <p class="person-title">President</p>
      <p class="address">Ashby Court, 42 Mercer Lane,<br>London N1 7QT</p>
      <ul class="contacts">
        <li>
          <svg viewBox="0 0 24 24" aria-hidden="true"><path d="M6.6 10.8a15.1 15.1 0 0 0 6.6 6.6l2.2-2.2c.3-.3.7-.4 1-.2 1.1.4 2.3.6 3.6.6.6 0 1 .4 1 1V20c0 .6-.4 1-1 1C10.6 21 3 13.4 3 4c0-.6.4-1 1-1h3.5c.6 0 1 .4 1 1 0 1.3.2 2.5.6 3.6.1.3 0 .7-.2 1z"/></svg>
          <span>020 7946 0318</span>
        </li>
        <li>
          <svg viewBox="0 0 24 24" aria-hidden="true"><path d="M2 6h20v12H2z"/><path d="M2 6l10 7 10-7v1.6l-10 7-10-7z" fill="#fff"/></svg>
          <span>info@gentlelinenlofts.com</span>
        </li>
        <li>
          <svg viewBox="0 0 24 24" aria-hidden="true"><circle cx="12" cy="12" r="10"/><path d="M7 6c2 1 3 2 2 4s1 3 3 3 1 3-1 5M15 4c-1 2 0 3 2 3s3 2 3 4" stroke="#fff" stroke-width="1.6" fill="none"/></svg>
          <span>www.gentlelinenlofts.com</span>
        </li>
      </ul>
    </div>

    <div class="footer-line"></div>
    <div class="footer-band"></div>
  </section>
</body>
</html>
```